Law Firm Website

We are a small California based law firm specializing in business, corporate and litigation matters. We need to have our website redesigned. We are looking for a new and fresh look for our site, keeping in mind that we are a law firm.
What we don't want:
**the traditional "gavel" and "scales of justice" look
**anything too crazy
What we do want:
**sophisticated yet modern and fresh corporate look and feel
**samples of websites we really like:
http://www.tarnwellhope.example
http://www.marrowgate.example/
we also like:
http://www.fenwoodastley.example/
http://www.qz.example/
http://www.brenhollow.example/
http://www.pvdn.example
http://www.nqrlaw.example/
The content will be whatever is currently on our website (www.okabelawgroup.example). We will be selecting the winner based on originality and keeping the above requirements in mind. Please note that the photos that you use will be the ones that we will be using, so choose wisely because the photos will make a difference.
Target Market(s)
Corporate clients
Industry/Entity Type
Law Firm
Look and feel

```html
<!DOCTYPE html>
<html lang="en">
<head>
<meta charset="utf-8">
<title>Okabe Law Group, LLP</title>
<link rel="stylesheet" href="https://fonts.googleapis.com/css2?family=Arimo:wght@400;700&family=Exo+2:wght@400;500&display=swap">
<style>
:root{
  --blue:#1a73d9;
  --blue-dark:#0d5bc0;
  --navy:#1d3f8f;
  --ink:#1c1c1c;
  --text:#2a2a2a;
  --muted:#555;
  --page:#f1f1f1;
  --panel:#f6f6f6;
  --dark:#2a2a2a;
  --footer:#2c2c2c;
  --line:#bdbdbd;
}
*{margin:0;padding:0;box-sizing:border-box}
html,body{width:1075px;height:1200px;overflow:hidden;background:var(--page)}
body{font-family:"Arimo",Arial,sans-serif;color:var(--text)}
.page{position:relative;width:1075px;height:1200px;overflow:hidden;background:var(--page)}
.abs{position:absolute}
.brand-square{left:154px;top:30px;width:70px;height:70px;background:var(--blue)}
.brand-name{left:245px;top:38px;font-size:26px;color:var(--ink);white-space:nowrap}
.brand-tag{left:247px;top:74px;font-size:16px;color:var(--ink)}
.call{left:769px;top:54px;display:flex;align-items:center;gap:10px;font-size:11px;color:var(--ink)}
.call-icon{width:24px;height:24px;border-radius:50%;background:#555;display:flex;align-items:center;justify-content:center}
.nav{left:154px;top:127px;width:768px;height:43px;background:linear-gradient(#2a86ea,var(--blue-dark));display:flex;align-items:center;font-size:11px;color:#fff}
.nav a{color:#fff;text-decoration:none}
.nav .home{width:72px;height:43px;background:linear-gradient(#4a4a4a,#1f1f1f);display:flex;align-items:center;justify-content:center;font-weight:700}
.nav .item{position:absolute;top:15px}
.hero-band{left:0;top:170px;width:1075px;height:350px;background:var(--dark)}
.hero-photo{left:154px;top:170px;width:768px;height:350px;background:linear-gradient(120deg,#3a1a0e 0%,#7a3a1c 35%,#a86a3a 55%,#4a2412 80%,#2a140a 100%)}
.welcome-box{left:631px;top:270px;width:251px;height:189px;background:var(--blue);border:2px solid #e8eef8;padding:18px 18px;color:#fff}
.welcome-box h2{font-family:"Exo 2",sans-serif;font-weight:400;font-size:13px;letter-spacing:.2px}
.welcome-box p{margin-top:24px;font-size:8.5px;line-height:18.5px;text-align:justify}
.dots{position:absolute;left:20px;bottom:18px;display:flex;gap:5px}
.dots span{width:10px;height:10px;border-radius:50%;background:#fff;border:2px solid #345}
.dots span.on{background:#e33;border-color:#fff;box-shadow:0 0 0 1px #345}
.services{left:154px;top:520px;width:768px;height:190px;background:var(--panel)}
.rule{left:154px;top:570px;width:768px;border-top:1px dashed #b8b8b8}
.service{position:absolute;top:531px;width:230px}
.service h3{display:flex;align-items:center;gap:14px;font-family:"Exo 2",sans-serif;font-weight:400;font-size:16px;color:var(--ink);height:30px}
.service p{margin-top:31px;font-size:9px;line-height:17px;text-align:justify;color:var(--ink)}
.btn{display:inline-flex;align-items:center;justify-content:center;color:#fff;font-size:11px;text-decoration:none}
.btn-read{position:absolute;left:0;top:123px;width:75px;height:32px;background:var(--blue);border:1px solid var(--blue-dark)}
.intro{left:153px;top:743px;width:383px;height:267px;background:#fff;border:1px solid #e2e2e2}
.intro-photo{position:absolute;left:0;top:0;width:381px;height:127px;background:linear-gradient(90deg,#4a3a30,#a99a88 45%,#e3ddd2 60%,#6a5a4e)}
.intro-caption{position:absolute;left:0;top:89px;width:381px;height:38px;background:rgba(215,210,200,.88);padding:8px 13px;font-family:"Exo 2",sans-serif;font-size:18px;color:var(--ink)}
.intro p{position:absolute;left:14px;top:143px;width:353px;font-size:9px;line-height:17px;text-align:justify;color:var(--ink)}
.btn-learn{position:absolute;left:13px;top:221px;width:73px;height:29px;background:var(--navy)}
.news-head{left:567px;top:743px;width:354px;height:35px;background:linear-gradient(#2a86ea,var(--blue-dark));color:#fff;font-family:"Exo 2",sans-serif;font-size:18px;padding:5px 14px}
.news{position:absolute;left:567px;width:354px;height:93px}
.news-photo{position:absolute;left:0;top:0;width:124px;height:93px;border:2px solid #222;background:linear-gradient(135deg,#2a3550,#8a95a8 50%,#d9a78a)}
.news-photo.portrait{background:linear-gradient(135deg,#e8e8e8,#b9a79a 50%,#3a3f4a)}
.news-num{position:absolute;right:0;bottom:0;width:28px;height:20px;background:var(--blue-dark);color:#fff;font-size:10px;display:flex;align-items:center;justify-content:center}
.news h4{position:absolute;left:146px;top:-2px;font-family:"Exo 2",sans-serif;font-weight:400;font-size:13px;color:var(--ink)}
.news time{position:absolute;left:145px;top:26px;font-family:"Exo 2",sans-serif;font-size:9px;color:var(--ink)}
.news p{position:absolute;left:144px;top:47px;width:210px;font-size:9px;line-height:17px;text-align:justify;color:var(--ink)}
.contact-bar{left:0;top:1045px;width:1075px;height:57px;background:#f8f8f8;border-top:1px solid #e0e0e0}
.contact{position:absolute;top:1065px;display:flex;align-items:center;gap:9px;font-size:10.5px;color:var(--ink)}
.footer{left:0;top:1102px;width:1075px;height:98px;background:var(--footer)}
.footer-square{left:154px;top:1125px;width:49px;height:49px;background:var(--blue)}
.copy{left:212px;top:1143px;font-size:11px;color:#ddd}
.social{position:absolute;top:1138px;width:20px;height:20px;border-radius:50%;background:#cfcfcf}
.footer-links{left:700px;top:1143px;font-size:9px;color:#ddd;white-space:nowrap}
.footer-links a{color:#ddd;text-decoration:none}
</style>
</head>
<body>
<div class="page">
  <header>
    <div class="abs brand-square" aria-hidden="true"></div>
    <div class="abs brand-name">Okabe Law Group, LLP</div>
    <div class="abs brand-tag">Attorneys at Law</div>
    <div class="abs call">
      <span class="call-icon"><svg width="13" height="13" viewBox="0 0 24 24"><path fill="#ddd" d="M6.6 10.8a15 15 0 0 0 6.6 6.6l2.2-2.2c.3-.3.7-.4 1-.2 1.1.4 2.3.6 3.6.6.6 0 1 .4 1 1V20c0 .6-.4 1-1 1A17 17 0 0 1 3 4c0-.6.4-1 1-1h3.5c.6 0 1 .4 1 1 0 1.3.2 2.5.6 3.6.1.3 0 .7-.2 1z"/></svg></span>
      <span>Call Us : (555) 014-2200</span>
    </div>
    <nav class="abs nav">
      <a class="home" href="#">Home</a>
      <a class="item" style="left:112px" href="#">About The Firm</a>
      <a class="item" style="left:249px" href="#">Practice Areas</a>
      <a class="item" style="left:379px" href="#">Links</a>
      <a class="item" style="left:464px" href="#">News and Events</a>
      <a class="item" style="left:595px" href="#">Contact us</a>
    </nav>
  </header>

  <section>
    <div class="abs hero-band"></div>
    <div class="abs hero-photo" role="img" aria-label="Photo of old leather-bound law books with reading glasses on an open book"></div>
    <div class="abs welcome-box">
      <h2>WELCOME TO OKABE LAW GROUP</h2>
      <p>Okabe Law Group, LLP provides quality legal representation to corporate as well as individual clients in the areas of business, corporate, securities, products liability, civil litigation</p>
      <div class="dots"><span class="on"></span><span></span><span></span><span></span></div>
    </div>
  </section>

  <section>
    <div class="abs services"></div>
    <div class="abs rule"></div>
    <div class="service" style="left:176px">
      <h3><svg width="20" height="20" viewBox="0 0 20 20"><g fill="none" stroke="#111" stroke-width="1.5"><path d="M10 2v15M5 17h10M3 5h14"/><path d="M3 5l-2.5 6h5zM17 5l-2.5 6h5z"/></g></svg>Civil Litigation</h3>
      <p>Serce wisi eturna aliquam volutpat adiscing duisac consequat non dui. Sed eget tortor ut neque sceleris-que vehicula pretium eget libero.</p>
      <a class="btn btn-read" href="#">Read More</a>
    </div>
    <div class="service" style="left:430px">
      <h3><svg width="26" height="20" viewBox="0 0 26 20"><g fill="#111"><rect x="2" y="15" width="14" height="4"/><rect x="7" y="3" width="8" height="6" transform="rotate(-35 11 6)"/><path d="M13 9l11 7-1 2-11-7z"/></g></svg>Employment Law</h3>
      <p>Serce wisi eturna aliquam volutpat adiscing duisac consequat non dui. Sed eget tortor ut neque sceleris-que vehicula pretium eget libero.</p>
      <a class="btn btn-read" href="#">Read More</a>
    </div>
    <div class="service" style="left:679px">
      <h3><svg width="20" height="20" viewBox="0 0 20 20"><g fill="#111"><path d="M10 1l9 4H1z"/><rect x="1" y="6" width="18" height="2"/><rect x="3" y="9" width="2.5" height="7"/><rect x="8.7" y="9" width="2.5" height="7"/><rect x="14.5" y="9" width="2.5" height="7"/><rect x="1" y="17" width="18" height="2"/></g></svg>Corporate Governance</h3>
      <p>Serce wisi eturna aliquam volutpat adiscing duisac consequat non dui. Sed eget tortor ut neque sceleris-que vehicula pretium eget libero.</p>
      <a class="btn btn-read" href="#">Read More</a>
    </div>
  </section>

  <section class="abs intro">
    <div class="intro-photo" role="img" aria-label="Photo of the firm's reception lobby and offices"></div>
    <div class="intro-caption">Welcome to Okabe Law Group, LLP</div>
    <p>Okabe Law Group, LLP provides quality legal representation to corporate as well as individual clients in the areas of business, corporate, securities, products liability, civil litigation (in State and Federal Courts), Alternative Dispute Resolution (arbitration and mediation), as well as a host of transactional matters.</p>
    <a class="btn btn-learn" href="#">Learn More</a>
  </section>

  <section>
    <div class="abs news-head">Latest News</div>
    <article class="news" style="top:796px">
      <div class="news-photo" role="img" aria-label="Photo of a businessman offering a handshake"><span class="news-num">12</span></div>
      <h4>Nulla laoreet justo vel</h4>
      <time>May 14, 2011</time>
      <p>Lorem ipsum dolor sit amet, consectetuer adipiscing elit, sed diam nonummy nibh euismod tincidunt ut laoreet dolore magna aliquam</p>
    </article>
    <article class="news" style="top:912px">
      <div class="news-photo portrait" role="img" aria-label="Photo of a smiling attorney"><span class="news-num">13</span></div>
      <h4>Nulla laoreet justo vel</h4>
      <time>May 14, 2011</time>
      <p>Lorem ipsum dolor sit amet, consectetuer adipiscing elit, sed diam nonummy nibh euismod tincidunt ut laoreet dolore magna aliquam</p>
    </article>
  </section>

  <footer>
    <div class="abs contact-bar"></div>
    <div class="contact" style="left:153px">
      <svg width="11" height="16" viewBox="0 0 11 16"><path fill="#222" d="M5.5 0A5.5 5.5 0 0 0 0 5.5C0 9.6 5.5 16 5.5 16S11 9.6 11 5.5A5.5 5.5 0 0 0 5.5 0zm0 7.6a2 2 0 1 1 0-4 2 2 0 0 1 0 4z"/></svg>
      <span>4100 Harbor Crest Drive, 8th Floor Lakeview, California 90000</span>
    </div>
    <div class="contact" style="left:507px">
      <svg width="12" height="12" viewBox="0 0 24 24"><path fill="#222" d="M6.6 10.8a15 15 0 0 0 6.6 6.6l2.2-2.2c.3-.3.7-.4 1-.2 1.1.4 2.3.6 3.6.6.6 0 1 .4 1 1V20c0 .6-.4 1-1 1A17 17 0 0 1 3 4c0-.6.4-1 1-1h3.5c.6 0 1 .4 1 1 0 1.3.2 2.5.6 3.6.1.3 0 .7-.2 1z"/></svg>
      <span>Tel : (555) 014-2200, &nbsp; (555) 014-2277</span>
    </div>
    <div class="contact" style="left:774px">
      <svg width="16" height="12" viewBox="0 0 16 12"><rect width="16" height="12" rx="1" fill="#222"/><path d="M1 1l7 5 7-5" fill="none" stroke="#f8f8f8" stroke-width="1.3"/></svg>
      <span>info@okabelawgroup.example</span>
    </div>
    <div class="abs footer"></div>
    <div class="abs footer-square" aria-hidden="true"></div>
    <div class="abs copy">© 2014 . All Rights Reserved.</div>
    <span class="social" style="left:473px"></span>
    <span class="social" style="left:502px"></span>
    <span class="social" style="left:532px"></span>
    <div class="abs footer-links"><a href="#">Home</a> &nbsp;| &nbsp; <a href="#">Practice Areas</a> &nbsp;| &nbsp;<a href="#">About</a> | <a href="#">Links</a> | &nbsp;<a href="#">Contact us</a></div>
  </footer>
</div>
</body>
</html>
```